Tralha Cesto Website

Tralha Cesto is a brazilian Self Storage in a Box where customers can store all the clutter that they have out of their houses. We deliver one or more boxes at their homes, they fill the boxes with their stuff and we store it for them.

"Tralha" means something like "mess" in portuguese. So the name would means something like "Mess Box" or "Clutter Box".

How it works:
1) The customer asks for 1 or more boxes.
2) Tralha Cesto leaves the boxes at their houses
3) The clients fill the boxes with their stuff
4) Customers call Tralha Cesto for the pick up
5) We get the boxes and store them
6) When the customer wants the box back they can order it online or by phone and wait for the box delivery.
-

We have already produced a flyer to launch the service. You can see this flyer at "Project Files".

We want the website to have a startup "look and fell". Here are some websites of similar services that we like very much.
- www.crateowl.example
- www.stowpod.example

We are planning this launching website to have only 2 pages. The Landing Page and a FAQ page. We are producing an explainer video. The proposed designs must think about a special place to place the video.

We are still writing it´s content but you can use the flyer as a reference.

Thanks.
Updates

Project Deadline Extended
Reason: The project was refundable but as we have already received good design options, now we are turning it to Non Refundable and giving more time for new designers to send their proposals. Thanks.

Project Deadline Extended

Target Market(s)

Young couples having kids
Students
Families in need of more space at home

Industry/Entity Type

Store

Requirements
Must have
• Special place to place the explainer video (still being produced).

How it works drawing. You can use the one on the flyer or draw a new one (recomended).

Transparent box drawings (showing it´s content). I will serve to show the clients what they can store with the service.

Clutter Room Before/After Pic/drawings (showing how the service can benefit the client).

```html
<!DOCTYPE html>
<html lang="pt">
<head>
<meta charset="utf-8">
<title>Tralha Cesto</title>
<link rel="stylesheet" href="https://fonts.googleapis.com/css2?family=Open+Sans:wght@400;600;700&display=swap">
<style>
:root{
  --orange:#f39a1e;
  --blue:#2f9ad6;
  --ink:#444;
  --muted:#777;
  --light:#f4f4f4;
  --gray:#dedede;
  --slate:#5d5d5d;
  --dark:#3a3a3a;
  --white:#fff;
}
*{margin:0;padding:0;box-sizing:border-box}
html,body{width:686px;height:1200px;overflow:hidden}
body{font-family:"Open Sans",Arial,sans-serif;color:var(--ink);background:var(--white);font-size:9px;line-height:1.45}
.site-header{height:40px;display:flex;align-items:center;justify-content:space-between;padding:0 88px 0 88px;position:relative}
.brand{display:flex;align-items:center;gap:6px;font-weight:700;font-size:15px;color:var(--orange)}
.brand-mark{width:14px;height:14px;border-radius:50%;background:var(--blue)}
.utility{position:absolute;top:3px;right:88px;display:flex;gap:8px;align-items:center;font-size:7px;color:var(--muted)}
.utility .search{width:58px;height:10px;border:1px solid #ccc}
.main-nav{display:flex;gap:14px;font-size:8.5px;margin-top:14px}
.main-nav a{color:var(--ink);text-decoration:none}
.hero{position:relative;height:326px}
.hero-photo{position:absolute;inset:0;background:linear-gradient(180deg,#6a5b4d 0%,#8a7663 45%,#b8a58c 75%,#d9d3c8 100%)}
.play{position:absolute;left:324px;top:118px;width:40px;height:40px}
.hero-band{position:absolute;left:0;right:0;bottom:0;height:96px;background:rgba(235,238,240,.82);text-align:center;padding-top:22px}
.hero-band h1{font-weight:400;font-size:19px;color:#555}
.btn{display:inline-block;border-radius:2px;color:var(--white);font-size:8px;padding:5px 18px;margin-top:8px}
.btn-blue{background:var(--blue)}
.btn-orange{background:var(--orange)}
.how{background:var(--gray);height:164px;padding:14px 88px 0}
.section-title{font-weight:400;font-size:15px;color:#555}
.steps{display:flex;justify-content:space-between;margin-top:14px}
.step{width:112px;display:flex;flex-direction:column;align-items:center}
.step-icons{display:flex;align-items:center;gap:10px;height:40px}
.num{width:36px;height:36px;border-radius:50%;border:2px solid var(--orange);color:var(--orange);font-size:17px;display:flex;align-items:center;justify-content:center}
.step p{font-size:7px;text-align:center;margin-top:8px;color:#555}
.contents{height:194px;display:flex;gap:22px;padding:16px 88px 0}
.box-art{width:220px;height:160px;background:linear-gradient(160deg,#f2f2f2,#cfcfcf);flex:none}
.contents h2{font-weight:400;font-size:15px;color:var(--blue);line-height:1.25}
.contents p{font-size:7.5px;color:var(--muted);margin-top:8px}
.before-after{background:var(--slate);height:212px;padding:8px 88px 0;display:flex;gap:18px}
.ba-item{flex:1;text-align:center;color:var(--white)}
.ba-photo{height:160px;background:linear-gradient(160deg,#3f4a55,#7b7f80 60%,#b9b3a4)}
.ba-item h3{font-weight:400;font-size:10px;margin-top:3px}
.ba-item p{font-size:6.5px;color:#ddd}
.welcome{text-align:center;padding:12px 92px 0;height:206px}
.welcome h2{font-weight:400;font-size:16px;color:var(--blue)}
.welcome p{font-size:7px;color:var(--muted);margin-top:6px}
.contact-card{margin:14px auto 0;width:150px;border:1px solid #ccc;padding:10px 0;color:var(--blue);font-size:9px;line-height:1.7}
.site-footer{background:var(--dark);height:58px;padding:10px 88px 0;display:flex;justify-content:space-between;color:#bbb;font-size:6.5px}
.foot-links{display:flex;gap:6px;margin-bottom:4px}
.social{display:flex;gap:4px;align-items:flex-start;flex-direction:column}
.social .dots{display:flex;gap:4px}
.social span.c{width:11px;height:11px;border-radius:50%;background:var(--blue)}
.social span.c.o{background:var(--orange)}
</style>
</head>
<body>
<header class="site-header">
  <div class="brand"><span class="brand-mark"></span>Tralha Cesto</div>
  <div class="utility"><span>(21) 5550 1234</span><span>Blog</span><span class="search"></span></div>
  <nav class="main-nav"><a href="#">Home</a><a href="#">How it works</a><a href="#">Pricing</a><a href="#">Security</a><a href="#">About Us</a><a href="#">Contact Us</a></nav>
</header>

<section class="hero">
  <div class="hero-photo" role="img" aria-label="Cluttered storage room full of boxes and household items"></div>
  <svg class="play" viewBox="0 0 40 40"><circle cx="20" cy="20" r="19" fill="rgba(255,255,255,.9)"/><path d="M16 12 L29 20 L16 28Z" fill="#333"/></svg>
  <div class="hero-band">
    <h1>It's easy to send your stuff to storage</h1>
    <a class="btn btn-blue">Get Started</a>
  </div>
</section>

<section class="how">
  <h2 class="section-title">How it Works</h2>
  <div class="steps">
    <div class="step"><div class="step-icons"><span class="num">1</span>
      <svg width="34" height="30" viewBox="0 0 34 30"><path d="M4 10 L17 4 L30 10 L30 24 L17 29 L4 24Z" fill="none" stroke="#555" stroke-width="2"/><path d="M4 10 L17 16 L30 10 M17 16 V29" fill="none" stroke="#555" stroke-width="2"/></svg></div>
      <p>Lorem Ipsum is simply dummy text of the printing and typesetting</p></div>
    <div class="step"><div class="step-icons"><span class="num">2</span>
      <svg width="40" height="30" viewBox="0 0 40 30"><rect x="2" y="8" width="22" height="14" fill="#555"/><path d="M24 12 H32 L37 17 V22 H24Z" fill="#555"/><circle cx="9" cy="24" r="3.5" fill="#555"/><circle cx="31" cy="24" r="3.5" fill="#555"/></svg></div>
      <p>Lorem Ipsum is simply dummy text of the printing and typesetting</p></div>
    <div class="step"><div class="step-icons"><span class="num">3</span>
      <svg width="34" height="30" viewBox="0 0 34 30"><rect x="4" y="10" width="26" height="18" fill="none" stroke="#555" stroke-width="2"/><path d="M4 10 L17 2 L30 10" fill="none" stroke="#555" stroke-width="2"/></svg></div>
      <p>Lorem Ipsum is simply dummy text of the printing and typesetting</p></div>
    <div class="step"><div class="step-icons"><span class="num">4</span>
      <svg width="34" height="30" viewBox="0 0 34 30"><rect x="3" y="4" width="28" height="24" fill="none" stroke="#555" stroke-width="2"/><path d="M3 12 H31 M3 20 H31 M17 4 V28" stroke="#555" stroke-width="2"/></svg></div>
      <p>Lorem Ipsum is simply dummy text of the printing and typesetting</p></div>
  </div>
</section>

<section class="contents">
  <div class="box-art" role="img" aria-label="Open transparent box showing stored belongings inside"></div>
  <div>
    <h2>Lorem Ipsum is simply dummy text of the printing and typesetting</h2>
    <p>Lorem Ipsum is simply dummy text of the printing and typesetting industry. Lorem Ipsum has been the industry's standard dummy text ever since the 1500s, when an unknown printer took a galley of type and scrambled it to make a type specimen book. It has survived not only five centuries, but also the leap into electronic typesetting, remaining essentially unchanged.</p>
    <a class="btn btn-orange">Read More</a>
  </div>
</section>

<section class="before-after">
  <div class="ba-item">
    <div class="ba-photo" role="img" aria-label="Messy room before using the service"></div>
    <h3>Before</h3>
    <p>Lorem Ipsum is simply dummy text of the printing and typesetting industry. Lorem Ipsum has been the industry's standard dummy text.</p>
  </div>
  <div class="ba-item">
    <div class="ba-photo" role="img" aria-label="Tidy room after using the service"></div>
    <h3>After</h3>
    <p>Lorem Ipsum is simply dummy text of the printing and typesetting industry. Lorem Ipsum has been the industry's standard dummy text.</p>
  </div>
</section>

<section class="welcome">
  <h2>Welcome to our site</h2>
  <p>Contrary to popular belief, Lorem Ipsum is not simply random text. It has roots in a piece of classical Latin literature from 45 BC, making it over 2000 years old. A Latin professor looked up one of the more obscure Latin words, consectetur, from a Lorem Ipsum passage, and going through the cites of the word in classical literature, discovered the undoubtable source. Lorem Ipsum comes from sections 1.10.32 and 1.10.33 of "de Finibus Bonorum et Malorum".</p>
  <div class="contact-card">Rua das Caixas, 140<br>(21) 5550 1234<br>tralhacesto.example</div>
</section>

<footer class="site-footer">
  <div>
    <div class="foot-links"><span>Home</span><span>How it works</span><span>Pricing</span><span>Security</span><span>About us</span><span>Contact Us</span></div>
    <div>Copyright © 2014 All Rights Reserved</div>
  </div>
  <div class="social"><span>Follow us</span><div class="dots"><span class="c"></span><span class="c"></span><span class="c o"></span></div></div>
</footer>
</body>
</html>
```